Corporate brochure design 4 pages

Hi,

We are a real estate company based in Europe.

We have almost finalized a rebranding.

We are developing a brand book guidelines (still on working process) to help you undertstand the look and feel of our new CI. I would like to receive proposals of design for a corporate brochure template. I need to receive the Indesign files with full ownership rights to be able to adapt all our documentation with this template.
Regarding the images, you can take gabaris on www.pelvarimages.example. I will be able to take them afterwards.

There will be 4 pages. you will receive the 4 pages on pdf for your consideration with our (almost) actual layout.

- 1st page: cover
- 2nd page: company presentation in french and english
- 3rd page: some market data + graph
- 4th page: 2 retail centers presentation.

In the template, i need to have:
- the paragraph styles in order
- 2 different masters with top/bottom/page number aso.

Please feel free to ask any other questions.

best regards,
Updates

I would like to precise tha t we are active on the commercial real estate sector:

- office transactions (rent /sales)
- property management of administrative and business buildings
- Valuation of properties
- Capital markets (investment advices for selling building)

Industry/Entity Type

Real Estate

Colors

Designer to choose colors to be used in the design.

```html
<!DOCTYPE html>
<html lang="en">
<head>
<meta charset="utf-8">
<title>Office Market Report Luxembourg Q3-2013 – Page 03</title>
<link href="https://fonts.googleapis.com/css2?family=Arimo:wght@400;700&display=swap" rel="stylesheet">
<style>
  :root {
    --orange: #f26522;
    --ink: #333333;
    --black: #111111;
    --panel: #e6e7e8;
    --row-alt: #efefef;
    --rule: #bdbdbd;
    --frame: #9a9a9a;
    --white: #ffffff;
  }
  * { box-sizing: border-box; margin: 0; padding: 0; }
  html, body { width: 873px; height: 1200px; overflow: hidden; background: var(--white); }
  body { font-family: "Arimo", Arial, sans-serif; color: var(--ink); position: relative; }

  .page-frame { position: absolute; left: 27px; top: 22px; width: 822px; height: 1160px; border: 1px solid var(--frame); }

  .running-head { position: absolute; top: 63px; right: 113px; font-size: 11px; color: var(--black); }
  .running-head .accent { color: var(--orange); }

  .section-title { position: absolute; left: 113px; font-size: 19px; font-weight: 700; line-height: 27px; color: var(--orange); }
  .section-title.market { top: 114px; width: 545px; }
  .section-title.graph { top: 682px; left: 111px; width: 520px; }

  .intro-text { position: absolute; left: 113px; top: 181px; width: 647px; font-size: 13px; line-height: 18.3px; text-align: justify; }

  .stock-panel { position: absolute; left: 110px; top: 297px; width: 226px; height: 350px; background: var(--panel); padding: 24px 14px 0 15px; }
  .stock-panel h3 { font-size: 17px; font-weight: 700; margin-bottom: 8px; }
  .stock-panel h3.fr { color: var(--orange); }
  .stock-panel h3.en { color: var(--black); margin-top: 22px; }
  .stock-panel p { font-size: 12px; line-height: 19.5px; text-align: justify; }

  .stock-table { position: absolute; left: 344px; top: 297px; width: 416px; table-layout: fixed; border-collapse: collapse; font-size: 9.5px; color: var(--ink); }
  .stock-table th { background: var(--orange); color: var(--white); font-weight: 700; height: 18px; text-align: left; padding: 0 4px 0 7px; border-left: 2px solid var(--white); white-space: nowrap; }
  .stock-table th:first-child { background: var(--white); border-left: 0; }
  .stock-table th.num { text-align: right; }
  .stock-table td { height: 13.5px; padding: 0 4px; vertical-align: middle; white-space: nowrap; overflow: hidden; }
  .stock-table tr:nth-child(even) td { background: var(--row-alt); }
  .stock-table td.zone { font-size: 8.5px; color: var(--black); padding-left: 3px; overflow: visible; }
  .stock-table td.num { text-align: right; }
  .stock-table tr.total td { font-weight: 700; color: var(--black); }
  .stock-table tr.total td.zone { font-weight: 400; }
  .stock-table tr.total td.label { text-align: right; padding-right: 12px; }
  .stock-table col.zone { width: 153px; }
  .stock-table col.district { width: 130px; }
  .stock-table col.m2 { width: 80px; }
  .stock-table col.pct { width: 53px; }

  .chart-panel { position: absolute; left: 110px; top: 753px; width: 422px; height: 264px; background: var(--panel); }
  .chart-panel svg { display: block; }
  .chart-panel text { font-family: "Arimo", Arial, sans-serif; }

  .side-text { position: absolute; left: 551px; top: 749px; width: 204px; font-size: 12.6px; line-height: 18.2px; text-align: justify; }
  .side-text p + p { margin-top: 10px; }

  .brand { position: absolute; left: 78px; top: 1094px; }
  .brand-name { font-size: 30px; font-weight: 400; letter-spacing: 1px; color: var(--black); line-height: 1; }
  .brand-tagline { margin-top: 6px; font-size: 9.5px; letter-spacing: 2px; color: var(--orange); }
  .footer-rule { position: absolute; left: 258px; top: 1128px; width: 512px; height: 1px; background: var(--rule); }
  .page-number { position: absolute; left: 780px; top: 1118px; font-size: 16px; font-weight: 700; color: var(--black); }
</style>
</head>
<body>
  <div class="page-frame"></div>

  <div class="running-head">Office Market Report <span class="accent">LUXEMBOURG</span>&nbsp; Q3-2013</div>

  <h2 class="section-title market">Lorem Ipsum. Proin gravida nibh vel recersp experruptiae velit auctor aliquet.</h2>

  <p class="intro-text">Lorem ipsum. Nam fugitio incte recersp iduntios eos experruptiae volum laccum quas molores sequi optatum entem fugit molorectore venis num volupta tiuntionest, nobis abo. Itas dolor apicim doloriatur? Met diat lab impos et rerferem volorepelest andam quam atempor epellaborest eat aut experibus, sit quam et volori beatem voloriae cori optat.Ictempore doluptatior sit voluptaqui demporibero ipic to tem lam que ium imporis tiusdae nis doluptae nus deriature sinus porerum harciis min con eiust aut ium re suntius.</p>

  <aside class="stock-panel">
    <h3 class="fr">STOCK</h3>
    <p>Le stock de mètres carrés disponibles de bureaux a augmenté de 0,36 % au troisième trimestre de cette année grâce à la livraison de près de 12 300 m². Le stock total équivaut à 3 465 600 m².</p>
    <h3 class="en">STOCK</h3>
    <p>The stock of available office square meters has increased by 0.36% during the third quarter of this year with the delivery of 12,300 m². The total stock reaches 3,465,600 sm².</p>
  </aside>

  <table class="stock-table">
    <colgroup><col class="zone"><col class="district"><col class="m2"><col class="pct"></colgroup>
    <thead>
      <tr><th></th><th>QUARTIERS-DISTRICTS</th><th class="num">STOCK M²</th><th class="num">STOCK %</th></tr>
    </thead>
    <tbody>
      <tr><td class="zone">CENTRE-VILLE (CITY)</td><td>Kirchberg</td><td class="num">915 000</td><td class="num">26,42 %</td></tr>
      <tr><td></td><td>CBD</td><td class="num">806 400</td><td class="num">23,27 %</td></tr>
      <tr><td></td><td>Station</td><td class="num">382 700</td><td class="num">11,04 %</td></tr>
      <tr><td></td><td>Cloche d'Or</td><td class="num">365 600</td><td class="num">10,55 %</td></tr>
      <tr><td></td><td>Limpertsberg</td><td class="num">85 000</td><td class="num">2,45 %</td></tr>
      <tr><td></td><td>Belair / Merl</td><td class="num">67 800</td><td class="num">1,96 %</td></tr>
      <tr><td></td><td>Hamm</td><td class="num">44 500</td><td class="num">1,28 %</td></tr>
      <tr><td></td><td>Kalchesbrück</td><td class="num">33 000</td><td class="num">0,95 %</td></tr>
      <tr class="total"><td></td><td class="label">TOTAL</td><td class="num">2 700 500</td><td class="num">77,92 %</td></tr>
      <tr><td class="zone">VILLE-PÉRIPHÉRIE (CITY-PERIPHERY)</td><td>Airport - Findel</td><td class="num">157 500</td><td class="num">4,54 %</td></tr>
      <tr><td></td><td>Bertrange / Bourmicht</td><td class="num">82 000</td><td class="num">2,37 %</td></tr>
      <tr><td></td><td>Strassen</td><td class="num">81 050</td><td class="num">2,34 %</td></tr>
      <tr><td></td><td>Howald</td><td class="num">62 600</td><td class="num">1,81 %</td></tr>
      <tr class="total"><td class="zone">PÉRIPHÉRIE (PERIPHERY)</td><td class="label">TOTAL</td><td class="num">383 150</td><td class="num">11,06 %</td></tr>
      <tr><td></td><td>Belval</td><td class="num">93 090</td><td class="num">2,69 %</td></tr>
      <tr><td></td><td>Capellen</td><td class="num">69 500</td><td class="num">2,01 %</td></tr>
      <tr><td></td><td>Leudelange</td><td class="num">73 556</td><td class="num">2,12 %</td></tr>
      <tr><td></td><td>Munsbach</td><td class="num">60 100</td><td class="num">1,73 %</td></tr>
      <tr><td></td><td>Windhof</td><td class="num">40 600</td><td class="num">1,17 %</td></tr>
      <tr><td></td><td>Esch-sur-Alzette</td><td class="num">24 700</td><td class="num">0,71 %</td></tr>
      <tr><td></td><td>Contern</td><td class="num">20 400</td><td class="num">0,59 %</td></tr>
      <tr class="total"><td></td><td class="label">TOTAL</td><td class="num">381 946</td><td class="num">11,02 %</td></tr>
      <tr><td></td><td></td><td></td><td></td></tr>
      <tr class="total"><td></td><td class="label">TOTAL</td><td class="num">3 465 596</td><td></td></tr>
    </tbody>
  </table>

  <h2 class="section-title graph">Lorem Ipsum. Proin gravida nibh vel dolor rerferem recersp experruptiae velit auctor aliquet.</h2>

  <figure class="chart-panel">
    <svg width="422" height="264" viewBox="110 753 422 264" aria-label="Office stock evolution 2003 to YTD 2013, in thousand m²">
      <rect x="124" y="770" width="394" height="223" fill="#ffffff"/>
      <text x="135" y="798" font-size="6.5" fill="#f26522" font-weight="700">000</text>
      <text x="136" y="804" font-size="6.5" fill="#f26522" font-weight="700">m²</text>
      <text x="337" y="800" font-size="12" fill="#222" text-anchor="middle">Lorem Ipsum. Proin gravida nibh vel aliquet.</text>
      <g stroke="#cfcfcf" stroke-width="0.8">
        <line x1="160" y1="822" x2="512" y2="822"/>
        <line x1="160" y1="845" x2="512" y2="845"/>
        <line x1="160" y1="868" x2="512" y2="868"/>
        <line x1="160" y1="890" x2="512" y2="890"/>
        <line x1="160" y1="913" x2="512" y2="913"/>
        <line x1="160" y1="936" x2="512" y2="936"/>
        <line x1="160" y1="958" x2="512" y2="958"/>
      </g>
      <g font-size="7" fill="#555">
        <text x="135" y="824">3.500</text>
        <text x="135" y="847">3.200</text>
        <text x="135" y="870">2.900</text>
        <text x="135" y="892">2.600</text>
        <text x="135" y="915">2.300</text>
        <text x="135" y="938">2.000</text>
        <text x="135" y="960">1.700</text>
      </g>
      <g fill="#f26522">
        <rect x="167" y="925" width="13" height="33"/>
        <rect x="199" y="904.5" width="13" height="53.5"/>
        <rect x="232" y="898.5" width="13" height="59.5"/>
        <rect x="265" y="892.5" width="13" height="65.5"/>
        <rect x="298" y="884.5" width="13" height="73.5"/>
        <rect x="331" y="862.5" width="13" height="95.5"/>
        <rect x="363" y="851" width="13" height="107"/>
        <rect x="396" y="843.5" width="13" height="114.5"/>
        <rect x="429" y="838.5" width="13" height="119.5"/>
        <rect x="462" y="833" width="13" height="125"/>
        <rect x="495" y="828.5" width="13" height="129.5"/>
      </g>
      <g font-size="5.5" fill="#555" text-anchor="middle">
        <text x="173.5" y="970">2003</text>
        <text x="205.5" y="970">2004</text>
        <text x="238.5" y="970">2005</text>
        <text x="271.5" y="970">2006</text>
        <text x="304.5" y="970">2007</text>
        <text x="337.5" y="970">2008</text>
        <text x="369.5" y="970">2009</text>
        <text x="402.5" y="970">2010</text>
        <text x="435.5" y="970">2011</text>
        <text x="468.5" y="970">2012</text>
        <text x="501.5" y="970">YTD 2013</text>
      </g>
      <text x="126" y="985" font-size="4" fill="#777">Source: Market research data</text>
      <text x="124" y="1007" font-size="11" fill="#333">Lorem Ipsum. Proin gravida nibh vel aliquet.</text>
      <line x1="464" y1="996" x2="464" y2="1013" stroke="#ffffff" stroke-width="1"/>
      <rect x="468" y="998" width="38" height="7" fill="#f26522"/>
      <text x="468" y="1012" font-size="4" fill="#666">Stock</text>
    </svg>
  </figure>

  <div class="side-text">
    <p>Lorem ipsum. incte recersp iduntios eos experruptiae volum laccum quas molores sequi optatum entem fugit molorectore venis num volupta tiuntionest, nobis abo.Met diat lab impos et rerferem volorepelest andam quam atempor epellaborest eat aut experibus,</p>
    <p>Ictempore doluptatior sit voluptaqui demporibero ipic to tem lam que ium imporis tiusdae nis doluptae nus deriature sinus porerum harciis min con eiust aut ium re suntius.</p>
  </div>

  <footer>
    <div class="brand">
      <div class="brand-name">ARVELLE</div>
      <div class="brand-tagline">COMMERCIAL REAL ESTATE</div>
    </div>
    <div class="footer-rule"></div>
    <div class="page-number">03</div>
  </footer>
</body>
</html>
```